Business Card Re-Design/Update

We'd like to update out business cards. I've included our current "Style guide" which has the colour scheme of the organisation in it. I've also included the branding files with logos etc in them.

I've also included a copy of one of our existing cards so that you can see how ugly/dated they look. I'd like a fresh modern corporate look.

Target Market(s)

These are for our clients, potential clients, industry contacts - like all business cards

Contact Information for Business Card

Name
Position
Company Address - Level 1, 47 Fernby Street, Carlow Qld 4072
Direct Phone
mobile
Email
Website -www.korvalit.com.au
Logo

Colors

Designer to choose colors to be used in the design.

Requirements
Must have
• Main Logo
• Cards will need to be editable to be able to personalize them for each new employee.
Nice to have
• The MapOut, ShipWell, KeepSteady would be okay to have if they can be sensibly and professionally added to the look without detracting from the main imagery.
• Maybe they could go on the back of the card? will leave this to your creative discretion as to whether/where they fit.
Should not have
• Should not have decorative or script fonts

```html
<!DOCTYPE html>
<html lang="en">
<head>
<meta charset="utf-8">
<title>korvalIT business card</title>
<link rel="stylesheet" href="https://fonts.googleapis.com/css2?family=Roboto:wght@400;500&family=Roboto+Condensed:wght@400;700&display=swap">
<style>
  :root {
    --backdrop: #2b2b2b;
    --card-front: #f4f4f4;
    --card-back: #231f20;
    --brand-red: #c4161c;
    --ink: #231f20;
    --ink-soft: #555555;
    --divider: #c9c9c9;
    --white: #ffffff;
  }
  * { margin: 0; padding: 0; box-sizing: border-box; }
  html, body { width: 1200px; height: 960px; overflow: hidden; background: var(--backdrop); }
  body { position: relative; font-family: "Roboto", Arial, sans-serif; }

  .card { position: absolute; left: 320px; width: 600px; }
  .card--front { top: 100px; height: 332px; background: var(--card-front); }
  .card--back { top: 492px; height: 342px; background: var(--card-back); }

  .brand { position: absolute; display: flex; align-items: center; }
  .brand__square { background: var(--brand-red); flex: none; }
  .brand__name { font-family: "Roboto", Arial, sans-serif; font-weight: 500; }

  .card--front .brand { left: 52px; top: 168px; gap: 12px; }
  .card--front .brand__square { width: 34px; height: 34px; }
  .card--front .brand__name { font-size: 30px; color: var(--ink); letter-spacing: -0.5px; }

  .divider { position: absolute; left: 311px; top: 78px; width: 1px; height: 208px; background: var(--divider); }

  .contact { position: absolute; left: 340px; top: 74px; }
  .contact__name { font-family: "Roboto Condensed", Arial, sans-serif; font-weight: 700; font-size: 21px; color: var(--brand-red); line-height: 24px; }
  .contact__role { font-family: "Roboto Condensed", Arial, sans-serif; font-size: 16px; color: var(--ink); line-height: 20px; }
  .contact__address { margin-top: 8px; font-size: 14.5px; color: var(--ink-soft); line-height: 18.5px; }
  .contact__list { list-style: none; margin-top: 12px; }
  .contact__item { display: flex; align-items: center; gap: 8px; font-size: 14.5px; color: var(--ink-soft); line-height: 19px; }
  .contact__icon { width: 14px; height: 14px; fill: var(--brand-red); flex: none; }

  .card--back .brand--hero { left: 0; right: 0; top: 94px; justify-content: center; gap: 20px; }
  .card--back .brand--hero .brand__square { width: 96px; height: 96px; background: var(--white); }
  .card--back .brand--hero .brand__name { font-size: 44px; color: var(--white); }

  .services { position: absolute; left: 0; right: 0; top: 274px; display: flex; justify-content: center; gap: 38px; list-style: none; }
  .services__item { display: flex; align-items: center; gap: 8px; font-weight: 500; font-size: 25px; color: var(--white); }
  .services__mark { width: 22px; height: 22px; background: var(--white); }
</style>
</head>
<body>
  <section class="card card--front" aria-label="Card front">
    <div class="brand">
      <span class="brand__square"></span>
      <span class="brand__name">korvalIT</span>
    </div>
    <span class="divider"></span>
    <div class="contact">
      <p class="contact__name">MAREN TALBOT</p>
      <p class="contact__role">Business Development Manager</p>
      <p class="contact__address">12/9 Larkin Ridge Road<br>Tenby QLD 4011</p>
      <ul class="contact__list">
        <li class="contact__item"><svg class="contact__icon" viewBox="0 0 16 16"><path d="M3.2 1l2.6 3.2-1.4 1.6c.8 2 2.6 3.8 4.6 4.6l1.6-1.4L13.8 11.6 12.4 14C6.6 13.6 2.4 9.4 2 3.6z"/></svg>+61 (0)7 3018 4420</li>
        <li class="contact__item"><svg class="contact__icon" viewBox="0 0 16 16"><path d="M3.2 1l2.6 3.2-1.4 1.6c.8 2 2.6 3.8 4.6 4.6l1.6-1.4L13.8 11.6 12.4 14C6.6 13.6 2.4 9.4 2 3.6z"/></svg>+61 (0)7 3018 4427</li>
        <li class="contact__item"><svg class="contact__icon" viewBox="0 0 16 16"><path d="M4.5 1h7a1 1 0 0 1 1 1v12a1 1 0 0 1-1 1h-7a1 1 0 0 1-1-1V2a1 1 0 0 1 1-1zm.8 2v9h5.4V3z"/></svg>+61 (0)412 605 938</li>
        <li class="contact__item"><svg class="contact__icon" viewBox="0 0 16 16"><path d="M4 1h6v4H4zM1 6h14v7H1zm2 2v1h3V8zm9 3v1h2v-1z"/></svg>+61 (0)7 3018 4401</li>
        <li class="contact__item"><svg class="contact__icon" viewBox="0 0 16 16"><path d="M1 3h14v10H1zm1.2 1.2L8 8.6l5.8-4.4z"/></svg>mtalbot@korvalit.com.au</li>
        <li class="contact__item"><svg class="contact__icon" viewBox="0 0 16 16"><path d="M8 1a7 7 0 1 0 0 14A7 7 0 0 0 8 1zm-1 2.2c-.6 1 .4 1.6 1.2 1.8 1 .2.6 1.4-.2 1.6-1 .2-2.6-.4-3 1-.4 1.2 1 1.6 1.4 2.6.3.8-.2 2-.4 2.4A5.5 5.5 0 0 1 7 3.2zm2.4 9.8c.4-1 1.4-1.6 1.2-2.8-.2-1 1.2-.8 2-1.4A5.5 5.5 0 0 1 9.4 13z"/></svg>www.korvalit.com.au</li>
      </ul>
    </div>
  </section>

  <section class="card card--back" aria-label="Card back">
    <div class="brand brand--hero">
      <span class="brand__square"></span>
      <span class="brand__name">korvalIT</span>
    </div>
    <ul class="services">
      <li class="services__item"><span class="services__mark"></span>MapOut</li>
      <li class="services__item"><span class="services__mark"></span>ShipWell</li>
      <li class="services__item"><span class="services__mark"></span>KeepSteady</li>
    </ul>
  </section>
</body>
</html>
```